Restyle corporate identity (+ logo) for a road construction company

We need a new logo and stationary design for our company VARNOK path. VARNOK path® increases the road base strength, while reducing major costs and time of road construction. Attached some examples of the current design.

Our wishes for the new logo:
- Business look
- Style sheet
- Modern

More information: www.varnokpath.example
Updates

Target Market(s)

Government

Industry/Entity Type

Construction

Requirements
Must have
• Logo (with road sign) + text

```html
<!DOCTYPE html>
<html lang="en">
<head>
<meta charset="utf-8">
<title>VARNOK path – Stationery</title>
<link rel="stylesheet" href="https://fonts.googleapis.com/css2?family=Source+Sans+3:wght@400;600&display=swap">
<style>
  :root{
    --backdrop:#d8d4cf;
    --paper:#e7e7e7;
    --band-grey:#a2a2a2;
    --flap-grey:#999999;
    --brand-green:#95c11f;
    --brand-text:#8a8a8a;
    --ink:#333333;
    --ink-soft:#4a4a4a;
    --ink-blue:#3a5aa8;
    --white:#ffffff;
  }
  *{box-sizing:border-box;margin:0;padding:0}
  html,body{width:1200px;height:809px;overflow:hidden;background:var(--backdrop)}
  body{font-family:"Source Sans 3",Arial,sans-serif;color:var(--ink)}
  .stage{position:relative;width:1200px;height:809px;overflow:hidden}

  /* Letterhead */
  .letterhead{position:absolute;left:54px;top:51px;width:496px;height:703px;background:var(--paper);box-shadow:0 2px 6px rgba(0,0,0,.25)}
  .band{position:absolute;left:0;width:100%;display:block}
  .band--top{top:0}
  .band--bottom{bottom:0}
  .band-url{position:absolute;color:var(--white);font-size:8.5px;letter-spacing:2.2px}
  .letterhead .band-url{right:25px;bottom:8px}

  .brand{position:absolute;display:flex;align-items:center}
  .brand-dot{border-radius:50%;background:var(--brand-green);flex:none}
  .brand-name{color:var(--brand-text);font-weight:600;letter-spacing:.5px;white-space:nowrap}
  .letterhead .brand{left:39px;top:66px}
  .letterhead .brand-dot{width:34px;height:34px;margin-right:11px}
  .letterhead .brand-name{font-size:19px}

  .contact{position:absolute;right:32px;top:48px;text-align:right;font-size:8.6px;line-height:13.2px;color:var(--ink-soft)}
  .contact-lines{margin-top:8px;line-height:14.5px}
  .contact-row{display:flex;justify-content:flex-end;align-items:center;gap:6px}
  .contact-row svg{width:10px;height:8px;flex:none}

  .letter{position:absolute;left:36px;top:226px;width:436px;font-size:8.4px;line-height:10.9px;color:var(--ink)}
  .letter-greeting{margin-bottom:21px}
  .letter p{margin-bottom:10.9px}
  .letter-signoff{margin-top:16px;line-height:12px}
  .signature{display:block;width:72px;height:28px;margin-top:12px;border-radius:4px;background:linear-gradient(90deg,rgba(58,90,168,.18),rgba(58,90,168,.08))}

  /* Envelope */
  .envelope{position:absolute;left:568px;top:395px;width:584px;height:359px}
  .envelope-flap{position:absolute;left:0;top:0;width:584px;height:100px;display:block}
  .flap-dot{position:absolute;left:266px;top:20px;width:52px;height:52px;border-radius:50%;background:var(--brand-green);border:3px solid var(--white)}
  .envelope-body{position:absolute;left:0;top:99px;width:584px;height:260px;background:var(--paper);box-shadow:0 2px 6px rgba(0,0,0,.25)}
  .envelope .brand{left:27px;top:39px}
  .envelope .brand-dot{width:42px;height:42px;margin-right:12px}
  .envelope .brand-name{font-size:22px}
  .envelope-address{position:absolute;left:28px;top:202px;font-size:8.8px;line-height:13px;color:var(--ink-soft)}
  .envelope .band-url{right:22px;bottom:6px}
</style>
</head>
<body>
<main class="stage">

  <section class="letterhead" aria-label="Letterhead">
    <svg class="band band--top" width="496" height="28" viewBox="0 0 496 28" aria-hidden="true">
      <polygon points="0,0 496,0 496,3 0,28" fill="var(--band-grey)"/>
    </svg>

    <div class="brand">
      <span class="brand-dot" aria-hidden="true"></span>
      <span class="brand-name">VARNOK path</span>
    </div>

    <address class="contact" style="font-style:normal">
      <div>Meridiaanweg 57</div>
      <div>2491 KT Veldhaven</div>
      <div>The Netherlands</div>
      <div class="contact-lines">
        <div class="contact-row">+31 70 555 01 24
          <svg viewBox="0 0 10 8" aria-hidden="true"><path d="M1 3 Q5 0 9 3 L8 4 L6.5 3 L6.5 2.4 Q5 2 3.5 2.4 L3.5 3 L2 4 Z M2.5 4.5 H7.5 L8.5 7.5 H1.5 Z" fill="var(--brand-green)"/></svg>
        </div>
        <div class="contact-row">info@varnokpath.example
          <svg viewBox="0 0 10 8" aria-hidden="true"><rect x="0.5" y="0.5" width="9" height="7" fill="var(--brand-green)"/><path d="M0.5 0.5 L5 4.5 L9.5 0.5" stroke="var(--paper)" stroke-width="0.8" fill="none"/></svg>
        </div>
      </div>
    </address>

    <article class="letter">
      <p class="letter-greeting">Dear Mr. Holt,</p>
      <p>Lorem ipsum dolor sit amet, consectetur adipiscing elit. Donec orci purus, luctus vitae dignissim eu, iaculis sed purus. Vivamus faucibus, ipsum nec aliquet viverra, leo mauris condimentum ligula, sit amet sagittis enim ligula quis arcu. Nam egestas tortor id nisi porttitor mattis. In tortor ante, ultricies in suscipit a, tempus non massa. Vivamus et auctor mi.</p>
      <p>Fusce vel massa nulla. Phasellus nec eros mauris, et scelerisque orci. Donec malesuada orci vitae nulla accumsan porta a id massa. Quisque accumsan iaculis magna sit amet fringilla. Maecenas consequat, magna eget tincidunt semper, odio nibh rutrum mi, id feugiat ante nisi eu risus. Vestibulum nunc orci, rhoncus a placerat in, ultricies in mi. Cras mattis varius eros, vel fringilla nisi suscipit eget.</p>
      <p>Quisque scelerisque sagittis nulla at porttitor. Mauris a justo et tellus interdum tristique. Sed id augue vitae urna euismod commodo aliquet a quam. Pellentesque arcu velit, cursus et malesuada ut, consequat et diam. Nullam erat sem, rhoncus id ullamcorper vitae, rhoncus et arcu. In ultricies ultricies nulla, ut rutrum nisi iaculis at. Donec eu magna a metus ornare faucibus.</p>
      <p>Fusce aliquet faucibus ultricies. Morbi semper, est id tincidunt gravida, sem arcu adipiscing lacus, ac bibendum nulla leo eu purus. Quisque nec diam sed risus consectetur a ccumsan quis quis nibh. Vestibulum id purus lorem.</p>
      <div class="letter-signoff">
        <div>Ruben Kasten</div>
        <div>Co-Founder &amp; CEO</div>
      </div>
      <span class="signature" role="img" aria-label="Handwritten signature in blue ink"></span>
    </article>

    <svg class="band band--bottom" width="496" height="31" viewBox="0 0 496 31" aria-hidden="true">
      <polygon points="0,29 496,0 496,31 0,31" fill="var(--brand-green)"/>
    </svg>
    <span class="band-url">www.varnokpath.example</span>
  </section>

  <section class="envelope" aria-label="Envelope">
    <svg class="envelope-flap" width="584" height="100" viewBox="0 0 584 100" aria-hidden="true">
      <path d="M0 100 L12 44 Q18 0 60 0 L544 0 Q576 0 578 34 L584 100 Z" fill="var(--flap-grey)"/>
    </svg>
    <span class="flap-dot" aria-hidden="true"></span>

    <div class="envelope-body">
      <svg class="band band--top" width="584" height="26" viewBox="0 0 584 26" aria-hidden="true">
        <polygon points="0,0 584,0 584,6 0,26" fill="var(--band-grey)"/>
      </svg>

      <div class="brand">
        <span class="brand-dot" aria-hidden="true"></span>
        <span class="brand-name">VARNOK path</span>
      </div>

      <address class="envelope-address" style="font-style:normal">
        <div>Meridiaanweg 57</div>
        <div>2491 KT Veldhaven</div>
        <div>The Netherlands</div>
      </address>

      <svg class="band band--bottom" width="584" height="32" viewBox="0 0 584 32" aria-hidden="true">
        <polygon points="0,30 584,0 584,32 0,32" fill="var(--brand-green)"/>
      </svg>
      <span class="band-url">www.varnokpath.example</span>
    </div>
  </section>

</main>
</body>
</html>
```